Etiketten-Design für nachhaltige Rasur- & Pflegeprodukte
> Wir suchen Verpackung und Etiketten für eine Marke für nachhaltige Rasur- & Pflegeprodukte.
Habedere liebe Designer,
„Habedere“ sagt man bei uns in Bayern, es bedeutet Hallo oder auf Wiedersehen, je nach Gelegenheit. In diesem Fall: Hallo.
Vielleicht kennst du uns schon, wir sind greenpines, wir betreiben einen kleinen Shop für Bartpflege & Rasur unter greenpines-shop.de und wir versuchen uns nun an einem neuen Thema: nachhaltige Rasur- & Pflegeprodukte für Frauen.
Das machen wir unter dem Namen „Sanft“.
Weil die Frage schon oft aufkam: Jawohl, wir haben uns dafür die Beine und die Achseln mit einem Rasierhobel rasiert.
> Zielgruppe.
Wir arbeiten an einer neuen Pflegelinie für Frauen, die sich vorwiegend mit der Rasur und den dazugehörigen Pflegeprodukten beschäftigt. Die Zielgruppe sind vor allem online-affine Frauen aus Deutschland, Österreich und der Schweiz, aber sicher auch europaweit im Alter von 21-45.
> Aufgabenstellung.
Wir sind auf der Suche nach einem Konzept für unsere Produktverpackungen bzw. Etiketten. Bei den Pflegeprodukten verzichten wir bewusst auf eine Umverpackung.
Konkret geplant sind ein Rasierhobel, dafür haben wir eine schöne Umverpackung. Außerdem starten wir mit Rasieröl, Rasierseife und einem After Shave Balsam. Es werden später noch andere Artikel dazukommen, eine Deocreme zum Beispiel.
Rasieröl, Rasiercreme und After Shave Balsam duften nach Orangen, es werden zwei oder drei weitere Duftrichtungen folgen, die eine wird beispielsweise nach Beeren duften, die andere nach Pfirsich und Mango – bitte beachte das bei der Erstellung des Konzeptes, die Unterschiede sollten später auf den ersten Blick erkennbar sein.
Zurück zum Thema Orange: Wir würden den Duft als leicht herben Zitrusduft bezeichnen.
> Die Maße.
• Umverpackung Rasierhobel, weißer Karton (165x90x40mm)
• Rasieröl 30ml (Etikett: 100x46mm)
• Rasiercreme 60ml (Etikett: 156x32mm)
• After Shave Balsam 60ml (Etikett: 156x32mm)
> Zwingend erforderliche Angaben.
Da es sich um Kosmetikprodukte handelt, sind einige Angaben auf dem Label zwingend erforderlich, beispielhaft sollen die folgenden Infos als Platzhalter dienen.
• Hergestellt für Friedrich Lautner e.K. von greenpines, Lindenhofweg 7, 83109 Kolbermoor
• Ingredients: Aqua, Stearic Acid, Cocos Nucifera oil, Glycerin, Potassium Hydroxide, Litsea Cubeba oil, (and) Citrus Sinensis Peel oil, Orbignya Oleifera oil, Sodium Hydroxide, Macadamia ternifolia oil, Talc, Kaolin, Citric Acid, Simmondsia chinensis oil, Maris sal, C.I. 77892 (and) Rad Clay, Citral, Limonene, Linalool, Geraniol
• Platz für einen Barcode
• Rasieröl sind 30ml / 1.01 FL.OZ. ODER Creme & Balsam jeweils 60ml / 2.03 FL. OZ.
Wir haben ein Bild der aktuellen Gefäße beigefügt, es kann aber durchaus sein, dass wir uns noch umen..

```html
<!DOCTYPE html>
<html lang="de">
<head>
<meta charset="utf-8">
<title>Sanft – Rasieröl Etiketten</title>
<link rel="stylesheet" href="https://fonts.googleapis.com/css2?family=Hind:wght@400;500&family=Federo&display=swap">
<style>
  :root {
    --page: #f1eeea;
    --paper: #ffffff;
    --dot: #8fb3a6;
    --ink: #2f4f45;
    --text: #3a3a3a;
    --berry: #6b2d63;
    --berry-soft: #dcc3e0;
    --mango: #f2b631;
    --mango-soft: #f8dfa0;
    --peach: #f3b56c;
    --peach-soft: #f6d8b8;
    --orange: #ea8c1a;
    --orange-soft: #f5d2a6;
  }
  * { box-sizing: border-box; margin: 0; padding: 0; }
  html, body { width: 667px; height: 1200px; overflow: hidden; background: var(--page); }
  body { font-family: "Hind", Arial, sans-serif; color: var(--text); }

  .sheet { width: 667px; height: 1200px; padding: 30px 27px; display: flex; flex-direction: column; }
  .scent-row { height: 285px; display: flex; align-items: center; gap: 28px; }

  .scent-beeren   { --accent: var(--berry);  --soft: var(--berry-soft);  --name: var(--berry); }
  .scent-mango    { --accent: var(--mango);  --soft: var(--mango-soft);  --name: #c98a10; }
  .scent-pfirsich { --accent: var(--peach);  --soft: var(--peach-soft);  --name: #d08a3c; }
  .scent-orange   { --accent: var(--orange); --soft: var(--orange-soft); --name: #c8740f; }

  /* brand name: plain text in one colour and weight, one plain dot beside it */
  .brand-name { display: flex; align-items: center; gap: 6px; font-family: "Hind", Arial, sans-serif; font-weight: 500; color: var(--ink); line-height: 1; position: relative; z-index: 1; }
  .brand-name::before { content: ""; border-radius: 50%; background: var(--dot); flex: none; }
  .brand-name.small { font-size: 10px; gap: 4px; }
  .brand-name.small::before { width: 7px; height: 7px; }
  .brand-name.large { font-size: 22px; }
  .brand-name.large::before { width: 10px; height: 10px; }

  /* flat bottle label 100 x 46 mm */
  .bottle-label { width: 432px; height: 199px; background: var(--paper); display: flex; position: relative; overflow: hidden; box-shadow: 0 1px 4px rgba(0,0,0,.08); }
  .label-back { width: 216px; padding: 12px 14px 10px; position: relative; border-right: 1px dashed #e2dede; }
  .label-front { width: 216px; position: relative; display: flex; flex-direction: column; align-items: center; padding-top: 34px; }

  .back-head { display: flex; align-items: flex-start; gap: 8px; }
  .back-title { text-align: right; flex: 1; line-height: 1.05; }
  .product-line { font-family: "Hind", Arial, sans-serif; color: var(--ink); position: relative; z-index: 1; }
  .back-title .product-line { font-size: 13px; }
  .scent-name { font-family: "Federo", "Hind", sans-serif; color: var(--name); position: relative; z-index: 1; }
  .back-title .scent-name { font-size: 11px; }

  .legal { font-size: 6.2px; line-height: 1.3; margin-top: 6px; text-align: center; }
  .ingredients-head { font-size: 6.2px; margin-top: 4px; }
  .ingredients { font-size: 6px; line-height: 1.35; text-align: justify; margin-top: 2px; }
  .volume { font-size: 7px; color: var(--text); position: relative; z-index: 1; }
  .label-back .volume { position: absolute; left: 14px; bottom: 10px; }

  .label-front .product-line { font-size: 18px; margin-top: 22px; }
  .label-front .scent-name { font-size: 21px; letter-spacing: 1px; line-height: 1.1; }
  .label-front .volume { margin-top: 8px; font-size: 6.5px; }

  .leaf-corner { position: absolute; top: 0; left: 0; width: 34px; height: 34px; border-bottom-right-radius: 34px; background: linear-gradient(135deg, var(--accent), var(--soft)); opacity: .85; }
  .soft-disc { position: absolute; border-radius: 50%; background: var(--soft); opacity: .75; }
  .block { position: absolute; background: var(--accent); }
  .band { position: absolute; left: 0; right: 0; bottom: 0; height: 14px; background: var(--soft); }

  /* folding box front */
  .carton-front { width: 150px; height: 262px; background: var(--paper); position: relative; overflow: hidden; display: flex; flex-direction: column; align-items: center; padding-top: 70px; box-shadow: 0 1px 4px rgba(0,0,0,.08); }
  .carton-front .leaf-corner { width: 40px; height: 40px; border-bottom-right-radius: 40px; }
  .carton-front .product-line { font-size: 17px; margin-top: 24px; }
  .carton-front .scent-name { font-size: 20px; letter-spacing: 1px; }
  .carton-front .volume { margin-top: 12px; font-size: 7px; }
  .top-bar { position: absolute; right: 12px; width: 16px; height: 7px; background: var(--accent); opacity: .7; }
</style>
</head>
<body>
<main class="sheet">

  <section class="scent-row scent-beeren">
    <div class="bottle-label">
      <div class="label-back">
        <div class="back-head">
          <div class="brand-name small">Sanft</div>
          <div class="back-title"><div class="product-line">Rasieröl sind</div><div class="scent-name">Beeren</div></div>
        </div>
        <p class="legal">Hergestellt für Friedrich Lautner e.K. von greenpines, Lindenhofweg 7, 83109 Kolbermoor.</p>
        <p class="ingredients-head">Ingredients:</p>
        <p class="ingredients">Aqua, Stearic Acid, Cocos Nucifera oil, Glycerin, Potassium Hydroxide, Litsea Cubeba oil, (and) Citrus Sinensis Peel oil, Orbignya Oleifera oil, Sodium Hydroxide, Macadamia ternifolia oil, Talc, Kaolin, Citric Acid, Simmondsia chinensis oil, Maris sal, C.I. 77892 (and) Rad Clay, Citral, Limonene, Linalool, Geraniol</p>
        <span class="volume">30 ml/1.01 FL.OZ.</span>
      </div>
      <div class="label-front">
        <div class="leaf-corner" role="img" aria-label="Blattzweig-Illustration in Beerentönen"></div>
        <div class="brand-name large">Sanft</div>
        <div class="product-line">Rasieröl sind</div>
        <div class="scent-name">Beeren</div>
        <div class="volume">30 ml/1.01 FL.OZ.</div>
        <div class="soft-disc" style="width:90px;height:90px;right:-20px;bottom:-50px"></div>
        <div class="band"></div>
        <div class="block" style="left:22px;bottom:0;width:30px;height:14px"></div>
        <div class="block" style="right:14px;bottom:14px;width:18px;height:10px;opacity:.7"></div>
      </div>
    </div>
    <div class="carton-front">
      <div class="leaf-corner" role="img" aria-label="Blattzweig-Illustration in Beerentönen"></div>
      <div class="top-bar" style="top:16px"></div><div class="top-bar" style="top:27px"></div>
      <div class="brand-name large">Sanft</div>
      <div class="product-line">Rasieröl sind</div>
      <div class="scent-name">Beeren</div>
      <div class="volume">30 ml/1.01 FL.OZ.</div>
      <div class="soft-disc" role="img" aria-label="Zarte Blattzweig-Illustration" style="width:100px;height:100px;left:40px;bottom:-36px"></div>
      <div class="block" style="right:0;bottom:44px;width:22px;height:10px"></div>
      <div class="block" style="left:20px;bottom:0;width:30px;height:10px;opacity:.7"></div>
    </div>
  </section>

  <section class="scent-row scent-mango">
    <div class="bottle-label">
      <div class="label-back">
        <div class="back-head">
          <div class="brand-name small">Sanft</div>
          <div class="back-title"><div class="product-line">Rasieröl sind</div><div class="scent-name">Mango</div></div>
        </div>
        <p class="legal">Hergestellt für Friedrich Lautner e.K. von greenpines, Lindenhofweg 7, 83109 Kolbermoor.</p>
        <p class="ingredients-head">Ingredients:</p>
        <p class="ingredients">Aqua, Stearic Acid, Cocos Nucifera oil, Glycerin, Potassium Hydroxide, Litsea Cubeba oil, (and) Citrus Sinensis Peel oil, Orbignya Oleifera oil, Sodium Hydroxide, Macadamia ternifolia oil, Talc, Kaolin, Citric Acid, Simmondsia chinensis oil, Maris sal, C.I. 77892 (and) Rad Clay, Citral, Limonene, Linalool, Geraniol</p>
        <span class="volume">30 ml/1.01 FL.OZ.</span>
      </div>
      <div class="label-front">
        <div class="leaf-corner" role="img" aria-label="Blattzweig-Illustration in Mangotönen"></div>
        <div class="brand-name large">Sanft</div>
        <div class="product-line">Rasieröl sind</div>
        <div class="scent-name">Mango</div>
        <div class="volume">30 ml/1.01 FL.OZ.</div>
        <div class="soft-disc" style="width:90px;height:90px;right:-20px;bottom:-50px;background:var(--peach-soft)"></div>
        <div class="band"></div>
        <div class="block" style="left:22px;bottom:0;width:30px;height:14px"></div>
        <div class="block" style="right:14px;bottom:14px;width:18px;height:10px;opacity:.7"></div>
      </div>
    </div>
    <div class="carton-front">
      <div class="leaf-corner" role="img" aria-label="Blattzweig-Illustration in Mangotönen"></div>
      <div class="top-bar" style="top:16px"></div><div class="top-bar" style="top:27px"></div>
      <div class="brand-name large">Sanft</div>
      <div class="product-line">Rasieröl sind</div>
      <div class="scent-name">Mango</div>
      <div class="volume">30 ml/1.01 FL.OZ.</div>
      <div class="soft-disc" role="img" aria-label="Zarte Blattzweig-Illustration" style="width:100px;height:100px;left:40px;bottom:-36px;background:var(--peach-soft)"></div>
      <div class="block" style="right:0;bottom:44px;width:22px;height:10px"></div>
      <div class="block" style="left:20px;bottom:0;width:30px;height:10px;opacity:.7"></div>
    </div>
  </section>

  <section class="scent-row scent-pfirsich">
    <div class="bottle-label">
      <div class="label-back">
        <div class="back-head">
          <div class="brand-name small">Sanft</div>
          <div class="back-title"><div class="product-line">Rasieröl sind</div><div class="scent-name">Pfirsich</div></div>
        </div>
        <p class="legal">Hergestellt für Friedrich Lautner e.K. von greenpines, Lindenhofweg 7, 83109 Kolbermoor.</p>
        <p class="ingredients-head">Ingredients:</p>
        <p class="ingredients">Aqua, Stearic Acid, Cocos Nucifera oil, Glycerin, Potassium Hydroxide, Litsea Cubeba oil, (and) Citrus Sinensis Peel oil, Orbignya Oleifera oil, Sodium Hydroxide, Macadamia ternifolia oil, Talc, Kaolin, Citric Acid, Simmondsia chinensis oil, Maris sal, C.I. 77892 (and) Rad Clay, Citral, Limonene, Linalool, Geraniol</p>
        <span class="volume">30 ml/1.01 FL.OZ.</span>
      </div>
      <div class="label-front">
        <div class="leaf-corner" role="img" aria-label="Blattzweig-Illustration in Pfirsichtönen"></div>
        <div class="brand-name large">Sanft</div>
        <div class="product-line">Rasieröl sind</div>
        <div class="scent-name">Pfirsich</div>
        <div class="volume">30 ml/1.01 FL.OZ.</div>
        <div class="soft-disc" style="width:90px;height:90px;right:-20px;bottom:-50px"></div>
        <div class="band"></div>
        <div class="block" style="left:22px;bottom:0;width:30px;height:14px"></div>
        <div class="block" style="right:14px;bottom:14px;width:18px;height:10px;opacity:.7"></div>
      </div>
    </div>
    <div class="carton-front">
      <div class="leaf-corner" role="img" aria-label="Blattzweig-Illustration in Pfirsichtönen"></div>
      <div class="top-bar" style="top:16px"></div><div class="top-bar" style="top:27px"></div>
      <div class="brand-name large">Sanft</div>
      <div class="product-line">Rasieröl sind</div>
      <div class="scent-name">Pfirsich</div>
      <div class="volume">30 ml/1.01 FL.OZ.</div>
      <div class="soft-disc" role="img" aria-label="Zarte Blattzweig-Illustration" style="width:100px;height:100px;left:40px;bottom:-36px"></div>
      <div class="block" style="right:0;bottom:44px;width:22px;height:10px"></div>
      <div class="block" style="left:20px;bottom:0;width:30px;height:10px;opacity:.7"></div>
    </div>
  </section>

  <section class="scent-row scent-orange">
    <div class="bottle-label">
      <div class="label-back">
        <div class="back-head">
          <div class="brand-name small">Sanft</div>
          <div class="back-title"><div class="product-line">Rasieröl sind</div><div class="scent-name">Orange</div></div>
        </div>
        <p class="legal">Hergestellt für Friedrich Lautner e.K. von greenpines, Lindenhofweg 7, 83109 Kolbermoor.</p>
        <p class="ingredients-head">Ingredients:</p>
        <p class="ingredients">Aqua, Stearic Acid, Cocos Nucifera oil, Glycerin, Potassium Hydroxide, Litsea Cubeba oil, (and) Citrus Sinensis Peel oil, Orbignya Oleifera oil, Sodium Hydroxide, Macadamia ternifolia oil, Talc, Kaolin, Citric Acid, Simmondsia chinensis oil, Maris sal, C.I. 77892 (and) Rad Clay, Citral, Limonene, Linalool, Geraniol</p>
        <span class="volume">30 ml/1.01 FL.OZ.</span>
      </div>
      <div class="label-front">
        <div class="leaf-corner" role="img" aria-label="Blattzweig-Illustration in Orangetönen"></div>
        <div class="brand-name large">Sanft</div>
        <div class="product-line">Rasieröl sind</div>
        <div class="scent-name">Orange</div>
        <div class="volume">30 ml/1.01 FL.OZ.</div>
        <div class="soft-disc" style="width:90px;height:90px;right:-20px;bottom:-50px"></div>
        <div class="band"></div>
        <div class="block" style="left:22px;bottom:0;width:30px;height:14px"></div>
        <div class="block" style="right:14px;bottom:14px;width:18px;height:10px;opacity:.7"></div>
      </div>
    </div>
    <div class="carton-front">
      <div class="leaf-corner" role="img" aria-label="Blattzweig-Illustration in Orangetönen"></div>
      <div class="top-bar" style="top:16px"></div><div class="top-bar" style="top:27px"></div>
      <div class="brand-name large">Sanft</div>
      <div class="product-line">Rasieröl sind</div>
      <div class="scent-name">Orange</div>
      <div class="volume">30 ml/1.01 FL.OZ.</div>
      <div class="soft-disc" role="img" aria-label="Zarte Blattzweig-Illustration" style="width:100px;height:100px;left:40px;bottom:-36px"></div>
      <div class="block" style="right:0;bottom:44px;width:22px;height:10px"></div>
      <div class="block" style="left:20px;bottom:0;width:30px;height:10px;opacity:.7"></div>
    </div>
  </section>

</main>
</body>
</html>
```